Need a Wordpress website for my HVAC company

I need a Wordpress website created for an HVAC company in a competitive market.
Following are some websites I like:
My current website is www.borvicoheating.com - we also have a facebook page with some pictures

We are an airconditioning and heating company that does both residential and commmercial work.
We need the following info on our website:
-mobile friendly
-Schedule an appt -repair/maintnenace/installation (i would like this option to always be on the page even if they scroll down.)
-24 hour service
-coupons /promotions
-financing
-reviews/testimonials
-about
-blog
-Our service area
The following are services we provide:
-Air conditioning - Installation/Service/Maintenance/new construction
-Heating - Installation/Service/Maintenance/new construction ( gas furnace, 2 stage furnace, electric heat)
-Duct - Repair/Replacement/Istallation - (zone systems)
-thermostats (wifi)
-Heat pump
-Air handler
-self communicating systems
-carbon monoxide testing
-hail damage
-duct sealing
-insulation
-Air cleaners - UV Air purifiers
-humidifiers

I would also like Quilbo SEO add on

Target Market(s)

Anyone who needs our services HVAC contractor

Industry/Entity Type

Hvac

Contact Information for Business Card

Phone:480-555-2046
website:www.borvicoheating.com
email pmarsh@borvicoheating.com

Coding

Coded - Design and coding required

Number of Pages Required

5+ page

Font styles to use
Serif
Sans Serif

Requirements
Must have
• I wrote in brief. I already have Webly Nest. Long story I paid for 3 years already. I need someone to put website there. Ive never used Wordpress but would like a template page so I can easily add services.
Nice to have
• Clean, bright, original

```html
<!DOCTYPE html>
<html lang="en">
<head>
<meta charset="utf-8">
<title>Borvico Heating &amp; Cooling</title>
<link href="https://fonts.googleapis.com/css2?family=Open+Sans:wght@400;600;700&display=swap" rel="stylesheet">
<style>
:root{
  --red:#c8202b;
  --red-dark:#9e1a22;
  --blue:#15599a;
  --ink:#333;
  --muted:#888;
  --soft:#f2f2f4;
  --line:#dcdcdc;
  --dark:#2b2b2b;
}
*{margin:0;padding:0;box-sizing:border-box}
html,body{width:1200px;height:2799px;overflow:hidden;background:#fff}
body{font-family:"Open Sans",Arial,sans-serif;color:var(--ink);position:relative}
.abs{position:absolute}
.section-title{position:absolute;left:0;width:1200px;text-align:center;color:var(--blue);font-weight:700;font-size:23px;letter-spacing:.3px}

/* header */
.brand{left:135px;top:42px;display:flex;align-items:center;gap:12px}
.brand-dot{width:44px;height:44px;border-radius:50%;background:var(--red)}
.brand-name{font-size:34px;font-weight:700;color:var(--blue);line-height:40px}
.brand-sub{font-size:13px;color:var(--blue);font-weight:600}
.header-info{right:135px;top:48px;text-align:right;font-size:13px;line-height:19px}
.header-info .call{font-size:25px;font-weight:700;color:var(--blue);margin-top:6px;display:flex;align-items:center;justify-content:flex-end;gap:6px}

/* nav */
.main-nav{top:177px;left:0;width:1200px;height:40px;background:var(--red)}
.main-nav a{position:absolute;top:0;height:40px;line-height:40px;color:#fff;font-size:12px;font-weight:600;text-decoration:none;text-transform:uppercase}
.main-nav a.active{background:var(--red-dark);padding:0 14px}

/* hero */
.hero{top:217px;left:0;width:1200px;height:397px;background:linear-gradient(90deg,#e4e7ea,#f1f3f5 60%,#e8ecef)}
.hero-photo{position:absolute;left:196px;top:10px;width:430px;height:380px;background:linear-gradient(160deg,#fbfbfb,#e3e6e9)}
.hero-figure{position:absolute;left:852px;top:28px;width:222px;height:369px;background:linear-gradient(180deg,#d9b28f 0,#d9b28f 32%,#2f64a8 32%,#1e4f8c)}
.hero-copy{position:absolute;right:365px;top:76px;text-align:right}
.hero-copy h1{color:var(--red);font-size:24px;line-height:30px;font-weight:700}
.hero-copy p{color:var(--blue);font-size:15px;font-weight:600;line-height:22px;margin-top:2px}
.arrow{position:absolute;width:20px;height:30px}

/* appointment */
.appointment{top:614px;left:0;width:1200px;height:362px;background:var(--soft)}
.tabs{position:absolute;left:424px;top:70px;height:44px;display:flex;border-bottom:3px solid var(--red)}
.tab{height:41px;line-height:41px;font-size:14px;color:#666;background:#fff;text-align:center;border:1px solid var(--line);border-bottom:0}
.tab.active{background:var(--red);color:#fff;border-color:var(--red);position:relative}
.tab.active::after{content:"";position:absolute;left:50%;bottom:-12px;margin-left:-9px;border:9px solid transparent;border-top-color:var(--red);border-bottom:0}
.field{position:absolute;height:43px;background:#fff;border:1px solid var(--line);font-size:12px;color:#999;padding:0 16px;line-height:41px}
.submit{position:absolute;left:562px;top:282px;width:76px;height:39px;background:var(--dark);color:#fff;font-size:12px;text-align:center;line-height:39px;font-weight:600}

/* features */
.feature{position:absolute;width:300px}
.feature .icon{height:28px;display:flex;align-items:center;margin-bottom:10px}
.feature h3{color:var(--red);font-size:18px;font-weight:400;line-height:22px}
.feature p{font-size:11px;line-height:16px;color:#666;margin-top:4px}

/* about */
.about-media{left:132px;top:1422px;width:456px;height:264px;border:1px solid var(--line);padding:10px;background:#fff}
.about-media div{width:100%;height:100%;background:linear-gradient(120deg,#eef0f2,#c9ced4 60%,#2f5f9c)}
.about-title{left:616px;top:1412px;color:var(--blue);font-weight:700;font-size:23px}
.about-text{left:616px;top:1455px;width:452px;font-size:13px;line-height:21px;color:#8a8a8a;text-align:justify}
.btn-outline{left:616px;top:1643px;width:97px;height:41px;border:1px solid #ccc;font-size:12px;text-align:center;line-height:39px;color:#555}

/* services */
.services{top:1750px;left:0;width:1200px;height:520px;background:var(--soft)}
.services-image{position:absolute;left:130px;top:110px;width:350px;height:410px;background:linear-gradient(180deg,#fdfdfd 0,#e6e6e8 55%,#e8c9ae 55%,#d7b291)}
.service-item{position:absolute;font-size:16px;display:flex;align-items:center;gap:10px;color:#333}
.btn{position:absolute;top:430px;height:46px;line-height:46px;color:#fff;font-size:14px;text-align:center}

/* testimonials */
.quote{left:0;width:1200px;text-align:center;top:2364px;font-size:17px;color:#444}
.quote-body{left:130px;width:940px;text-align:center;top:2393px;font-size:12px;line-height:20px;color:#999}
.avatar{left:512px;top:2448px;width:56px;height:56px;border-radius:50%;background:#d6d8db}
.person{left:584px;top:2456px;font-size:15px;color:#444}
.stars{left:584px;top:2480px;display:flex;gap:2px}

/* footer */
.footer{top:2570px;left:0;width:1200px;height:160px;background:var(--soft)}
.footer h4{position:absolute;font-size:12px;font-weight:700;color:#333}
.footer ul{position:absolute;list-style:none;font-size:11px;line-height:22px;color:#555}
.footer ul li::before{content:"• ";color:#999}
.contact li::before{content:""!important}
.contact li{display:flex;align-items:center;gap:8px}
.card{position:absolute;top:56px;width:36px;height:20px;background:#d9dadd;border:1px solid #c5c6c9}
.copyright{left:135px;top:2754px;font-size:12px;color:#444}
.social{position:absolute;top:2750px;width:26px;height:26px;border-radius:50%;background:#9aa0a8}
</style>
</head>
<body>

<header>
  <div class="abs brand">
    <span class="brand-dot"></span>
    <div><div class="brand-name">Borvico</div><div class="brand-sub">Heating &amp; Cooling</div></div>
  </div>
  <div class="abs header-info">
    <div>24 hours a day ~ 7 days a week</div>
    <div style="font-size:14px">Service with Intefrity</div>
    <div class="call">
      <svg width="12" height="18" viewBox="0 0 12 18"><rect x="1" y="1" width="10" height="16" rx="2" fill="none" stroke="#15599a" stroke-width="2"/><circle cx="6" cy="14" r="1" fill="#15599a"/></svg>
      Call (480) 555-2046
    </div>
  </div>
</header>

<nav class="abs main-nav">
  <a class="active" style="left:135px">&#8962; Home</a>
  <a style="left:253px">About us</a>
  <a style="left:367px">24 hour services</a>
  <a style="left:532px">Coupons</a>
  <a style="left:647px">Financing</a>
  <a style="left:768px">Reviews</a>
  <a style="left:876px">Blog</a>
  <a style="left:964px">Contact us</a>
</nav>

<section class="abs hero">
  <div class="hero-photo" role="img" aria-label="Wall-mounted air conditioning unit"></div>
  <div class="hero-figure" role="img" aria-label="Cartoon technician holding a thermometer and giving a thumbs up"></div>
  <div class="hero-copy">
    <h1>YOUR SATISFACTION IS<br>GUARANTEED</h1>
    <p>Our Reputation Depends on it</p>
  </div>
  <svg class="arrow" style="left:22px;top:183px" viewBox="0 0 20 30"><path d="M15 3 4 15l11 12" fill="none" stroke="#888" stroke-width="4"/></svg>
  <svg class="arrow" style="left:1158px;top:183px" viewBox="0 0 20 30"><path d="M5 3l11 12L5 27" fill="none" stroke="#888" stroke-width="4"/></svg>
</section>

<section class="abs appointment">
  <h2 class="section-title" style="top:30px">SCHEDULE AN APPOINTMENT</h2>
  <div class="tabs">
    <div class="tab active" style="width:126px">Installation</div>
    <div class="tab" style="width:133px">Maintenance</div>
    <div class="tab" style="width:93px">Repair</div>
  </div>
  <div class="field" style="left:132px;top:153px;width:218px">Name</div>
  <div class="field" style="left:370px;top:153px;width:218px">Email</div>
  <div class="field" style="left:608px;top:153px;width:219px">Phone</div>
  <div class="field" style="left:847px;top:153px;width:219px">Service for<svg style="position:absolute;right:14px;top:17px" width="10" height="7" viewBox="0 0 10 7"><path d="M1 1l4 4 4-4" fill="none" stroke="#888" stroke-width="1.5"/></svg></div>
  <div class="field" style="left:132px;top:218px;width:456px">Address</div>
  <div class="field" style="left:608px;top:218px;width:458px">Message</div>
  <div class="submit">SUBMIT</div>
</section>

<section>
  <h2 class="section-title" style="top:1028px">WHY CHOOSE US</h2>
  <div class="feature" style="left:132px;top:1093px">
    <div class="icon"><svg width="24" height="24" viewBox="0 0 24 24"><circle cx="12" cy="12" r="10" fill="none" stroke="#c8202b" stroke-width="2.5"/><path d="M12 6v6l-4 3" fill="none" stroke="#c8202b" stroke-width="2.5"/></svg></div>
    <h3>24/7 Emergency Service</h3>
    <p>You need air conditioning service when you need it, not when we feel like being open. Call now. No need to wait!</p>
  </div>
  <div class="feature" style="left:457px;top:1093px">
    <div class="icon"><svg width="26" height="26" viewBox="0 0 26 26"><rect x="2" y="4" width="22" height="20" fill="none" stroke="#c8202b" stroke-width="2.5"/><path d="M2 10h22M8 1v6M18 1v6M7 14h3M12 14h3M17 14h3M7 19h3M12 19h3" stroke="#c8202b" stroke-width="2"/></svg></div>
    <h3>Same Day Service</h3>
    <p>You deserve a fast solution to your problem. We provide it - right away.</p>
  </div>
  <div class="feature" style="left:783px;top:1093px">
    <div class="icon"><svg width="34" height="26" viewBox="0 0 34 26"><circle cx="17" cy="7" r="5" fill="#c8202b"/><circle cx="6" cy="10" r="4" fill="#c8202b"/><circle cx="28" cy="10" r="4" fill="#c8202b"/><path d="M9 26c0-8 16-8 16 0zM0 24c0-6 10-7 10-1v1zM24 24c0-6 10-5 10 0z" fill="#c8202b"/></svg></div>
    <h3>Highly Trained Technicians</h3>
    <p>will install or repair your brand air conditioning and heating system for top reliability, energy savings, and property value.</p>
  </div>
  <div class="feature" style="left:132px;top:1228px">
    <div class="icon"><svg width="20" height="28" viewBox="0 0 20 28"><path d="M12 0 2 16h7l-3 12 12-17h-7z" fill="#c8202b"/></svg></div>
    <h3>Free Energy Survey</h3>
    <p>for replacement air conditioning and heating systems. Let us help you get maximum comfort and savings. No obligation.</p>
  </div>
  <div class="feature" style="left:457px;top:1228px">
    <div class="icon"><svg width="34" height="26" viewBox="0 0 34 26"><rect x="2" y="4" width="30" height="20" fill="none" stroke="#c8202b" stroke-width="2.5"/><circle cx="17" cy="14" r="6" fill="#c8202b"/></svg></div>
    <h3>Pay by the Job, Not by the Hour</h3>
    <p>our up-front, flat rate pricing lets you know exactly what to expect for your air conditioning service or replacement.</p>
  </div>
  <div class="feature" style="left:783px;top:1228px">
    <div class="icon"><svg width="28" height="28" viewBox="0 0 28 28"><rect x="1" y="12" width="6" height="15" fill="#c8202b"/><path d="M9 13 15 2c3 0 4 3 3 7h8c2 0 3 2 2 4l-3 12c-1 2-2 2-3 2H9z" fill="#c8202b"/></svg></div>
    <h3>Fairness and Honesty</h3>
    <p>Our technicians do not work on commission, which allows us to keep our prices down. That also means you can trust your technician to give you honest answers that are best for you and your families or businesses comfort.</p>
  </div>
</section>

<section>
  <div class="abs about-media"><div role="img" aria-label="Technician servicing an air conditioning unit, video thumbnail"></div></div>
  <h2 class="abs about-title">ABOUT US</h2>
  <p class="abs about-text">Sed arcu justo, consectetur nec sapien et, pulvinar vestibulum nulla. Proin sodales, risus vitae fermentum faucibus, enim nunc elementum magna, in venenatis dui ligula ac justo. Quisque rhoncus tempor metus, eu porttitor nunc malesuada nec. Cras dolor ipsum, elementum non felis id, euismod egestas lorem. Vivamus id fringilla erat, a vestibulum arcu. Sed lobortis, dui eget tristique commodo, nulla dolor posuere turpis, ac fringilla sapien nulla et tortor. Sed auctor dolor neque, non bibendum velit sodales sit amet. Nulla gravida suscipit tortor, vel tristique lacus.</p>
  <div class="abs btn-outline">Read more</div>
</section>

<section class="abs services">
  <h2 class="section-title" style="top:44px">SERVICES WE PROVIDE ARE</h2>
  <div class="services-image" role="img" aria-label="Hand pressing a digital wall thermostat"></div>
  <div class="service-item" style="left:545px;top:118px"><svg width="14" height="14" viewBox="0 0 14 14"><circle cx="7" cy="7" r="6" fill="none" stroke="#333" stroke-width="1.6"/><path d="M4 7l2 2 4-4" fill="none" stroke="#333" stroke-width="1.6"/></svg>Air conditioning</div>
  <div class="service-item" style="left:545px;top:162px"><svg width="14" height="14" viewBox="0 0 14 14"><circle cx="7" cy="7" r="6" fill="none" stroke="#333" stroke-width="1.6"/><path d="M4 7l2 2 4-4" fill="none" stroke="#333" stroke-width="1.6"/></svg>Heating</div>
  <div class="service-item" style="left:545px;top:206px"><svg width="14" height="14" viewBox="0 0 14 14"><circle cx="7" cy="7" r="6" fill="none" stroke="#333" stroke-width="1.6"/><path d="M4 7l2 2 4-4" fill="none" stroke="#333" stroke-width="1.6"/></svg>Duct</div>
  <div class="service-item" style="left:545px;top:250px"><svg width="14" height="14" viewBox="0 0 14 14"><circle cx="7" cy="7" r="6" fill="none" stroke="#333" stroke-width="1.6"/><path d="M4 7l2 2 4-4" fill="none" stroke="#333" stroke-width="1.6"/></svg>Thermostats</div>
  <div class="service-item" style="left:545px;top:294px"><svg width="14" height="14" viewBox="0 0 14 14"><circle cx="7" cy="7" r="6" fill="none" stroke="#333" stroke-width="1.6"/><path d="M4 7l2 2 4-4" fill="none" stroke="#333" stroke-width="1.6"/></svg>Heat pump</div>
  <div class="service-item" style="left:545px;top:338px"><svg width="14" height="14" viewBox="0 0 14 14"><circle cx="7" cy="7" r="6" fill="none" stroke="#333" stroke-width="1.6"/><path d="M4 7l2 2 4-4" fill="none" stroke="#333" stroke-width="1.6"/></svg>Air handler</div>
  <div class="service-item" style="left:545px;top:382px"><svg width="14" height="14" viewBox="0 0 14 14"><circle cx="7" cy="7" r="6" fill="none" stroke="#333" stroke-width="1.6"/><path d="M4 7l2 2 4-4" fill="none" stroke="#333" stroke-width="1.6"/></svg>Self communicating systems</div>
  <div class="service-item" style="left:840px;top:118px"><svg width="14" height="14" viewBox="0 0 14 14"><circle cx="7" cy="7" r="6" fill="none" stroke="#333" stroke-width="1.6"/><path d="M4 7l2 2 4-4" fill="none" stroke="#333" stroke-width="1.6"/></svg>carbon monoxide testing</div>
  <div class="service-item" style="left:840px;top:162px"><svg width="14" height="14" viewBox="0 0 14 14"><circle cx="7" cy="7" r="6" fill="none" stroke="#333" stroke-width="1.6"/><path d="M4 7l2 2 4-4" fill="none" stroke="#333" stroke-width="1.6"/></svg>Hail damage</div>
  <div class="service-item" style="left:840px;top:206px"><svg width="14" height="14" viewBox="0 0 14 14"><circle cx="7" cy="7" r="6" fill="none" stroke="#333" stroke-width="1.6"/><path d="M4 7l2 2 4-4" fill="none" stroke="#333" stroke-width="1.6"/></svg>Duct sealing</div>
  <div class="service-item" style="left:840px;top:250px"><svg width="14" height="14" viewBox="0 0 14 14"><circle cx="7" cy="7" r="6" fill="none" stroke="#333" stroke-width="1.6"/><path d="M4 7l2 2 4-4" fill="none" stroke="#333" stroke-width="1.6"/></svg>Insulation</div>
  <div class="service-item" style="left:840px;top:294px"><svg width="14" height="14" viewBox="0 0 14 14"><circle cx="7" cy="7" r="6" fill="none" stroke="#333" stroke-width="1.6"/><path d="M4 7l2 2 4-4" fill="none" stroke="#333" stroke-width="1.6"/></svg>Air cleaners</div>
  <div class="service-item" style="left:840px;top:338px"><svg width="14" height="14" viewBox="0 0 14 14"><circle cx="7" cy="7" r="6" fill="none" stroke="#333" stroke-width="1.6"/><path d="M4 7l2 2 4-4" fill="none" stroke="#333" stroke-width="1.6"/></svg>Humidifiers</div>
  <div class="btn" style="left:545px;width:215px;background:var(--red)">Book for Residential Service</div>
  <div class="btn" style="left:793px;width:232px;background:var(--blue)">Book for Commercial Service</div>
</section>

<section>
  <h2 class="section-title" style="top:2324px">TESTIMONIALS</h2>
  <p class="abs quote"><span style="color:#aaa;font-size:24px;font-weight:700">&ldquo;</span> Pellentesque convallis molestie enim sit amet efficitur amet consequat risus.</p>
  <p class="abs quote-body">Nullam accumsan purus vel tempus viverra. Mauris suscipit felis id nunc elementum varius. Praesent elementum nulla sit amet justo pellentesque scelerisque. Nam et tortor in ante iaculis porttitor in luctus mi. Vivamus gravida sem a pretium euismod. Nam lobortis, purus et. <span style="color:#aaa;font-size:24px;font-weight:700">&rdquo;</span></p>
  <div class="abs avatar" role="img" aria-label="Customer portrait"></div>
  <div class="abs person">Marta Linn, City</div>
  <div class="abs stars">
    <svg width="98" height="16" viewBox="0 0 98 16"><g fill="#f2b01e"><path id="st" d="M8 0l2.4 5 5.5.6-4.1 3.7 1.2 5.4L8 12l-5 2.7 1.2-5.4L.1 5.6 5.6 5z"/><use href="#st" x="20"/><use href="#st" x="40"/><use href="#st" x="60"/><use href="#st" x="80"/></g></svg>
  </div>
  <svg class="arrow" style="left:20px;top:2403px" viewBox="0 0 20 30"><path d="M15 3 4 15l11 12" fill="none" stroke="#999" stroke-width="3"/></svg>
  <svg class="arrow" style="left:1160px;top:2403px" viewBox="0 0 20 30"><path d="M5 3l11 12L5 27" fill="none" stroke="#999" stroke-width="3"/></svg>
</section>

<footer class="abs footer">
  <div class="abs" style="left:135px;top:36px;display:flex;align-items:center;gap:10px">
    <span style="width:30px;height:30px;border-radius:50%;background:#777;display:block"></span>
    <span style="font-size:22px;font-weight:700;color:#555">Borvico</span>
  </div>
  <h4 style="left:309px;top:26px">LINKS</h4>
  <ul style="left:309px;top:44px"><li>Home</li><li>About us</li><li>24 hour services</li><li>Coupons</li></ul>
  <ul style="left:445px;top:44px"><li>Financing</li><li>Reviews</li><li>Blog</li><li>Contact us</li></ul>
  <h4 style="left:582px;top:26px">CONTACT INFO</h4>
  <ul class="contact" style="left:582px;top:44px">
    <li><svg width="8" height="11" viewBox="0 0 8 11"><path d="M4 0a4 4 0 0 0-4 4c0 3 4 7 4 7s4-4 4-7a4 4 0 0 0-4-4z" fill="#555"/></svg>24 Building name, Street name, City - Zipcode</li>
    <li><svg width="8" height="11" viewBox="0 0 8 11"><rect x="1" y="0" width="6" height="11" rx="1" fill="#555"/></svg>Phone : (480) 555-2046</li>
    <li><svg width="10" height="8" viewBox="0 0 10 8"><rect width="10" height="8" fill="#555"/><path d="M0 0l5 4 5-4" fill="none" stroke="#fff"/></svg>Email : info@borvicoheating.com</li>
  </ul>
  <h4 style="left:880px;top:26px">WE ACCEPT ALL CREDIT CARDS</h4>
  <div class="card" style="left:880px"></div>
  <div class="card" style="left:922px"></div>
  <div class="card" style="left:964px"></div>
  <div class="card" style="left:1006px"></div>
</footer>

<p class="abs copyright">Copyright &copy; 2016 Company name. All rights reserved.</p>
<span class="social" style="left:932px"></span>
<span class="social" style="left:962px"></span>
<span class="social" style="left:992px"></span>
<span class="social" style="left:1022px"></span>

</body>
</html>
```